Pelican HVAC WordPress website design

Design a new modern, clean, website for HVAC mechanical business that uses company logo/colors for branding and recognition. Files attached are just for band and color information. Here is a website design that appeals to me https://www.corvellsupply.example/

A clear description of who we are and what we do

An easily-navigated site map

An easily-navigated site map for mobile devices

Easy-to-find contact information

Obvious call to action for service, installs or to schedule estimates

about us page

Provide a way for potential customers to contact us via text or email

provide a way that allows a customer to upload a picture to request a service call or quote.
Updates

I'm looking for the design to be completed in WordPress

Industry/Entity Type

HVAC Mechanical & Building Automation / Controls contractor

Coding

Coded - Design and coding required

Number of Pages Required

5+ page

Colors
0054AA
0677BA
7BADD7
CADEEF
E8F1F8

Requirements
Must have
• Design a new modern, clean, website for HVAC mechanical business that uses company logo/colors for branding and recognition. Files attached are just for band and color information. Here is a website design that appeals to me https://www.corvellsupply.example/ A clear description of who we are and what we do An easily-navigated site map An easily-navigated site map for mobile devices Easy-to-find contact information Obvious call to action for service, installs or to schedule estimates about us page Provide a way for potential customers to contact us via text or email provide a way that allows a customer to upload a picture to request a service call or quote.
Nice to have

```html
<!DOCTYPE html>
<html lang="en">
<head>
<meta charset="UTF-8">
<title>Pelican HVAC</title>
<link rel="stylesheet" href="https://fonts.googleapis.com/css2?family=Josefin+Sans:wght@400;600;700&family=League+Spartan:wght@400;500;600&family=Montserrat:wght@400;500;600;700;800&display=swap">
<style>
:root{
  --navy:#0a3372;
  --blue:#0054AA;
  --blue-mid:#0677BA;
  --blue-soft:#7BADD7;
  --blue-pale:#CADEEF;
  --blue-mist:#E8F1F8;
  --deep:#033a7a;
  --ink:#1b1b1b;
  --muted:#444;
  --white:#fff;
  --black:#000;
}
*{margin:0;padding:0;box-sizing:border-box}
html,body{width:1200px;height:4444px;overflow:hidden}
body{position:relative;background:var(--white);font-family:"Montserrat",sans-serif;color:var(--ink)}
.abs{position:absolute}
.btn{position:absolute;display:flex;align-items:center;justify-content:center;background:var(--deep);color:var(--white);font-family:"Montserrat",sans-serif;font-weight:800;font-size:13px;letter-spacing:.5px;border-radius:20px}
.photo{position:absolute}

/* top bar + header */
.topbar{position:absolute;left:0;top:0;width:1200px;height:64px;background:linear-gradient(90deg,#0a3372,#0054AA 60%,#0a3372)}
.topbar .item{position:absolute;top:24px;color:var(--white);font-weight:800;font-size:12.5px;letter-spacing:1px}
.topbar svg{position:absolute;top:18px}
.header{position:absolute;left:0;top:64px;width:1200px;height:86px;background:var(--white);box-shadow:0 2px 6px rgba(0,0,0,.06)}
.brand{position:absolute;left:109px;top:22px;width:220px;height:108px;border-radius:50%;background:var(--white);border:4px solid var(--blue);box-shadow:0 2px 8px rgba(0,0,0,.2);display:flex;align-items:center;justify-content:center;font-family:"Montserrat",sans-serif;font-weight:800;font-size:24px;color:var(--blue);z-index:2}
.nav a{position:absolute;top:100px;font-size:14px;color:#333;text-decoration:none;letter-spacing:.5px}

/* hero */
.hero{position:absolute;left:0;top:150px;width:1200px;height:569px;background:linear-gradient(100deg,#23303c 0%,#3c4d5c 40%,#7d95ab 70%,#a9bfd2 100%)}
.hero .kicker{position:absolute;left:114px;top:130px;font-family:"Josefin Sans",sans-serif;font-size:31px;letter-spacing:3px;color:var(--white)}
.hero h1{position:absolute;left:113px;top:180px;font-family:"Josefin Sans",sans-serif;font-weight:700;font-size:44px;letter-spacing:4px;color:var(--white)}
.hero p{position:absolute;left:114px;top:244px;width:420px;font-size:12px;font-weight:700;line-height:21px;color:var(--white)}

/* about */
.eyebrow{font-family:"Montserrat",sans-serif;font-size:15px;letter-spacing:1px;color:#222}
.section-title{font-family:"Josefin Sans",sans-serif;font-weight:700;font-size:36px;letter-spacing:2px;color:var(--ink)}
.section-title span{color:var(--blue)}
.about-text{position:absolute;left:647px;width:445px;font-size:12.5px;line-height:24px;color:#333;letter-spacing:.3px}

/* works */
.works-band{position:absolute;left:0;top:1276px;width:1200px;height:460px;background:linear-gradient(180deg,var(--blue) 0%,#00458f 60%,#003a7a 100%)}
.card{position:absolute;z-index:3;top:1457px;width:312px;height:310px;background:var(--white);box-shadow:0 4px 14px rgba(0,0,0,.15)}
.card .img{position:absolute;left:10px;top:10px;width:292px;height:242px}
.card .label{position:absolute;left:20px;top:273px;font-size:14.5px;font-weight:600;letter-spacing:1px;color:#222}
.card svg{position:absolute;right:14px;top:276px}

/* services */
.services-bg{position:absolute;left:0;top:1736px;width:1200px;height:640px;background:linear-gradient(180deg,#eef3f9 0%,#f6f9fc 40%,#e8eef5 100%)}
.svc{position:absolute;top:1964px;width:240px;text-align:center}
.svc .name{margin-top:14px;font-size:14px;letter-spacing:1.5px;line-height:22px;color:#222}
.svc .arrow{margin-top:12px}
.divider{position:absolute;top:1974px;width:0;height:170px;border-left:2px dashed #222}

/* stats */
.stat{position:absolute;font-family:"League Spartan",sans-serif;font-weight:500;font-size:30px;line-height:31px;color:var(--white)}
.stat-sep{position:absolute;top:2445px;width:3px;height:110px;background:var(--white)}

/* testimonial */
.t-heading{position:absolute;left:110px;top:2716px;font-family:"League Spartan",sans-serif;font-weight:500;font-size:35px;color:var(--ink)}
.t-heading span{color:var(--blue)}

/* quote */
.field{position:absolute;height:56px;border:2px solid var(--white);border-radius:28px;color:var(--white);font-size:13px;padding-left:22px;display:flex;align-items:center}
.field svg{position:absolute;right:20px}

/* footer */
.footer{position:absolute;left:0;top:4061px;width:1200px;height:383px;background:var(--black);color:var(--white)}
.footer h4{position:absolute;font-family:"Josefin Sans",sans-serif;font-weight:600;font-size:18px;letter-spacing:1.5px}
.footer .link{position:absolute;font-size:13px;letter-spacing:1px}
.footer .contact{position:absolute;font-size:13px;letter-spacing:1px}
</style>
</head>
<body>

<!-- top bar -->
<div class="topbar">
  <div class="item" style="left:373px">CONTACT US VIA TEXT OR EMAIL</div>
  <svg style="left:673px" width="30" height="30" viewBox="0 0 30 30"><circle cx="15" cy="15" r="13" fill="none" stroke="#fff" stroke-width="2"/><path d="M10 9c1-1 2-1 3 1l1 2c0 1-1 2-1 2 1 2 2 3 4 4 0 0 1-1 2-1l2 1c2 1 2 2 1 3-1 1-3 2-5 1-4-2-7-5-8-9 0-2 0-3 1-4z" fill="#fff"/></svg>
  <div class="item" style="left:728px">555 - 014 - 2287</div>
  <svg style="left:894px" width="30" height="30" viewBox="0 0 30 30"><circle cx="15" cy="15" r="13" fill="none" stroke="#fff" stroke-width="2"/><rect x="8.5" y="10" width="13" height="10" rx="1.5" fill="none" stroke="#fff" stroke-width="1.8"/><path d="M9 11l6 5 6-5" fill="none" stroke="#fff" stroke-width="1.8"/></svg>
  <div class="item" style="left:951px">info@pelicanhvac.example</div>
</div>
<div class="header"></div>
<div class="brand">Pelican HVAC</div>
<nav class="nav">
  <a style="left:524px">Home</a>
  <a style="left:620px">About Us</a>
  <a style="left:743px">Services</a>
  <a style="left:862px">Team</a>
</nav>
<div class="btn" style="left:955px;top:86px;width:134px;height:38px">Contact Us</div>

<!-- hero -->
<section class="hero" role="img" aria-label="Photo of a technician in a hard hat servicing a rooftop air conditioning unit">
  <div class="kicker">Welcome To</div>
  <h1>PELICAN HVAC</h1>
  <p>Lorem ipsum dolor sit amet, consectetur adipiscing elit, sed do eiusmod tempor incididunt ut labore et dolore magna aliqua.</p>
</section>
<div class="btn" style="left:112px;top:479px;width:202px;height:34px">Schedule an Service</div>

<!-- about -->
<div class="photo" style="left:110px;top:810px;width:252px;height:376px;border-radius:10px;background:linear-gradient(160deg,#e9e6df,#c9c2b4)" role="img" aria-label="Photo of a technician on a ladder installing a wall air conditioner"></div>
<div class="photo" style="left:367px;top:812px;width:236px;height:185px;border-radius:10px;background:linear-gradient(160deg,#cfd9e2,#6f8aa2)" role="img" aria-label="Photo of a technician cleaning an indoor air conditioning unit"></div>
<div class="photo" style="left:367px;top:1005px;width:236px;height:184px;border-radius:10px;background:linear-gradient(160deg,#8a8d90,#3e4246)" role="img" aria-label="Photo of a technician repairing an outdoor condenser"></div>
<div class="abs eyebrow" style="left:647px;top:832px">Who We Are?</div>
<div class="abs section-title" style="left:645px;top:858px">About <span>Us</span></div>
<p class="about-text" style="top:912px">Lorem ipsum dolor sit amet, consectetur adipiscing elit, sed do eiusmod tempor incididunt ut labore et dolore magna aliqua. Ut enim ad minim veniam, quis nostrud exercitation ullamco laboris nisi ut aliquip ex ea commodo consequat.</p>
<p class="about-text" style="top:1019px">Duis aute irure dolor in reprehenderit in voluptate velit esse cillum dolore eu fugiat nulla pariatur. Excepteur sint occaecat cupidatat non proident, sunt in culpa qui officia deserunt mollit anim id est laborum.</p>
<div class="btn" style="left:643px;top:1134px;width:134px;height:36px">Read More</div>

<!-- works -->
<div class="works-band"></div>
<div class="services-bg" role="img" aria-label="Faded photo of a technician working on HVAC equipment"></div>
<svg class="abs" style="left:0;top:1560px" width="1200" height="180" viewBox="0 0 1200 180"><path d="M0 165 Q600 -40 1200 165 L1200 180 L0 180Z" fill="#eef3f9"/></svg>
<div class="abs eyebrow" style="left:0;width:1200px;text-align:center;top:1340px;color:#fff;font-size:14px">Our Works</div>
<div class="abs section-title" style="left:0;width:1200px;text-align:center;top:1367px;color:#fff;font-size:35px">What We Do</div>

<div class="card" style="left:110px">
  <div class="img" style="background:linear-gradient(150deg,#5c6066,#b7463d)" role="img" aria-label="Photo of a technician working on a furnace"></div>
  <div class="label">Heating</div>
  <svg width="18" height="14" viewBox="0 0 18 14"><path d="M1 7h15M11 2l5 5-5 5" fill="none" stroke="#0054AA" stroke-width="2"/></svg>
</div>
<div class="card" style="left:443px">
  <div class="img" style="background:linear-gradient(150deg,#d9dcdf,#7e8690)" role="img" aria-label="Photo of a technician in a hard hat servicing a ceiling ventilation unit"></div>
  <div class="label">Ventilation</div>
  <svg width="18" height="14" viewBox="0 0 18 14"><path d="M1 7h15M11 2l5 5-5 5" fill="none" stroke="#0054AA" stroke-width="2"/></svg>
</div>
<div class="card" style="left:776px">
  <div class="img" style="background:linear-gradient(150deg,#9cc3e6,#c9b8a0)" role="img" aria-label="Photo of a technician installing an outdoor air conditioning unit"></div>
  <div class="label">Air Conditioning</div>
  <svg width="18" height="14" viewBox="0 0 18 14"><path d="M1 7h15M11 2l5 5-5 5" fill="none" stroke="#0054AA" stroke-width="2"/></svg>
</div>

<!-- services -->
<div class="abs section-title" style="left:0;width:1200px;text-align:center;top:1850px;font-size:35px">Our <span>Services</span></div>

<div class="svc" style="left:110px">
  <svg width="74" height="74" viewBox="0 0 74 74"><path d="M37 6l7 4 8-2 3 8 8 4-2 8 4 7-4 7 2 8-8 4-3 8-8-2-7 4-7-4-8 2-3-8-8-4 2-8-4-7 4-7-2-8 8-4 3-8 8 2z" fill="#0054AA"/><circle cx="37" cy="37" r="18" fill="#eef3f9"/><path d="M25 37l9 9 24-24" fill="none" stroke="#0a3372" stroke-width="7"/></svg>
  <div class="name">INSTALLATION OF<br>HEATING, AIR<br>CONDITIONING,</div>
  <div class="arrow"><svg width="18" height="12" viewBox="0 0 18 12"><path d="M1 6h15M11 1l5 5-5 5" fill="none" stroke="#0054AA" stroke-width="2"/></svg></div>
</div>
<div class="divider" style="left:362px"></div>
<div class="svc" style="left:368px">
  <svg width="74" height="74" viewBox="0 0 74 74"><path d="M37 6l7 4 8-2 3 8 8 4-2 8 4 7-4 7 2 8-8 4-3 8-8-2-7 4-7-4-8 2-3-8-8-4 2-8-4-7 4-7-2-8 8-4 3-8 8 2z" fill="#0054AA"/><circle cx="37" cy="37" r="17" fill="#eef3f9"/><path d="M28 46l12-12m2-8a6 6 0 1 0 6 6" fill="none" stroke="#0a3372" stroke-width="6" stroke-linecap="round"/></svg>
  <div class="name">HEATING AND AIR<br>CONDITIONING<br>REPAIR</div>
  <div class="arrow"><svg width="18" height="12" viewBox="0 0 18 12"><path d="M1 6h15M11 1l5 5-5 5" fill="none" stroke="#0054AA" stroke-width="2"/></svg></div>
</div>
<div class="divider" style="left:602px"></div>
<div class="svc" style="left:625px">
  <svg width="74" height="74" viewBox="0 0 74 74"><path d="M14 60l34-34" stroke="#0054AA" stroke-width="9" stroke-linecap="round"/><circle cx="54" cy="20" r="11" fill="none" stroke="#0054AA" stroke-width="7"/><path d="M18 14l42 42" stroke="#0a3372" stroke-width="8" stroke-linecap="round"/><rect x="10" y="8" width="14" height="10" rx="2" transform="rotate(45 17 13)" fill="#0a3372"/></svg>
  <div class="name">MAINTENANCE<br>SERVICES FOR HVAC<br>SYSTEMS</div>
  <div class="arrow"><svg width="18" height="12" viewBox="0 0 18 12"><path d="M1 6h15M11 1l5 5-5 5" fill="none" stroke="#0054AA" stroke-width="2"/></svg></div>
</div>
<div class="divider" style="left:884px"></div>
<div class="svc" style="left:883px">
  <svg width="74" height="74" viewBox="0 0 74 74"><rect x="14" y="10" width="30" height="54" rx="4" fill="#0054AA"/><rect x="19" y="16" width="20" height="14" fill="#eef3f9"/><path d="M31 36l-6 10h6l-3 9 9-12h-6l3-7z" fill="#eef3f9"/><path d="M44 40h6c3 0 4 2 4 4v10c0 3 4 3 4 0V26" fill="none" stroke="#0a3372" stroke-width="4"/><rect x="52" y="14" width="12" height="14" rx="2" fill="#0a3372"/></svg>
  <div class="name">ELECTRICAL<br>SERVICES</div>
  <div class="arrow" style="margin-top:34px"><svg width="18" height="12" viewBox="0 0 18 12"><path d="M1 6h15M11 1l5 5-5 5" fill="none" stroke="#0054AA" stroke-width="2"/></svg></div>
</div>
<div class="btn" style="left:541px;top:2219px;width:119px;height:36px;border-radius:18px">View All</div>

<!-- stats -->
<svg class="abs" style="left:0;top:2320px" width="1200" height="340" viewBox="0 0 1200 340"><defs><linearGradient id="statGrad" x1="0" y1="0" x2="0" y2="1"><stop offset="0" stop-color="#0054AA"/><stop offset="1" stop-color="#003a7a"/></linearGradient></defs><path d="M0 110 Q600 -40 1200 110 L1200 340 L0 340Z" fill="url(#statGrad)"/></svg>
<div class="abs" style="left:152px;top:2457px;font-size:14px;color:#fff">Our Statistics</div>
<div class="stat" style="left:152px;top:2484px;font-size:33px;line-height:36px">Some Important<br>Facts</div>
<div class="stat" style="left:483px;top:2458px">10+ Years<br>Experience</div>
<div class="stat-sep" style="left:650px"></div>
<div class="stat" style="left:717px;top:2458px">100+<br>Projects<br>Completed</div>
<div class="stat-sep" style="left:896px"></div>
<div class="stat" style="left:972px;top:2458px">50+<br>Clients</div>

<!-- testimonials -->
<div class="photo" style="left:564px;top:2605px;width:636px;height:542px;background:linear-gradient(160deg,#8fb8e0 0%,#5b7fa6 45%,#3b4f66 100%)" role="img" aria-label="Photo of a technician in a hard hat testing wiring on a rooftop unit"></div>
<div class="abs" style="left:0;top:2655px;width:660px;height:492px;background:#fff"></div>
<div class="abs" style="left:110px;top:2685px;font-size:15px;color:#222">Testimonials</div>
<div class="t-heading">What Our <span>Client</span> says?</div>
<div class="abs" style="left:108px;top:2772px;font-family:'Josefin Sans',sans-serif;font-weight:700;font-size:40px;color:#0054AA">&ldquo;</div>
<div class="photo" style="left:138px;top:2776px;width:90px;height:90px;border-radius:50%;background:linear-gradient(160deg,#f1ddd0,#b58a74);box-shadow:0 2px 8px rgba(0,0,0,.2)" role="img" aria-label="Client portrait"></div>
<div class="abs" style="left:250px;top:2798px;font-size:16px;color:#222">Renata</div>
<div class="abs" style="left:248px;top:2820px;font-size:11px;letter-spacing:1px;color:#e8b21c">&#9733;&#9733;&#9733;&#9733;&#9733;</div>
<p class="abs" style="left:121px;top:2888px;width:360px;font-size:13px;line-height:27.5px;color:#222">Lorem ipsum dolor sit amet, consectetur adipiscing elit, sed do eiusmod tempor incididunt ut labore et dolore magna aliqua. Ut enim ad minim veniam, quis nostrud exercitation ullamco laboris nisi ut aliquip ex ea commodo consequat.</p>
<svg class="abs" style="left:119px;top:3055px" width="44" height="10" viewBox="0 0 44 10"><circle cx="5" cy="5" r="3.5" fill="#0054AA"/><circle cx="16" cy="5" r="3" fill="#bbb"/><circle cx="26" cy="5" r="3" fill="#bbb"/><circle cx="36" cy="5" r="3" fill="#bbb"/></svg>

<!-- request a quote -->
<div class="photo" style="left:0;top:3236px;width:471px;height:492px;background:linear-gradient(150deg,#5e6c78,#a9b3bc 50%,#6e3b2f)" role="img" aria-label="Photo of two engineers in hard hats inspecting pipework"></div>
<div class="abs" style="left:471px;top:3236px;width:729px;height:492px;background:linear-gradient(180deg,#0054AA,#003a7a)"></div>
<div class="abs" style="left:526px;top:3288px;font-family:'League Spartan',sans-serif;font-weight:500;font-size:34px;color:#fff">Request a Quote</div>
<div class="field" style="left:517px;top:3353px;width:262px">Name</div>
<div class="field" style="left:810px;top:3353px;width:264px">Phone</div>
<div class="field" style="left:519px;top:3422px;width:552px">Email</div>
<div class="field" style="left:519px;top:3490px;width:552px">Select Service
  <svg width="14" height="10" viewBox="0 0 14 10"><path d="M2 3l5 5 5-5" fill="none" stroke="#fff" stroke-width="2"/></svg></div>
<div class="field" style="left:519px;top:3558px;width:552px">Upload Picture
  <svg width="26" height="22" viewBox="0 0 26 22"><rect x="1" y="4" width="20" height="16" rx="2" fill="none" stroke="#fff" stroke-width="2"/><path d="M3 18l6-7 4 4 3-3 4 6" fill="none" stroke="#fff" stroke-width="2"/><path d="M22 1v8M18 5h8" stroke="#fff" stroke-width="2"/></svg></div>
<div class="btn" style="left:526px;top:3641px;width:134px;height:40px;background:#fff;color:#111;border-radius:20px">Submit</div>

<!-- newsletter -->
<div class="abs eyebrow" style="left:0;width:1200px;text-align:center;top:3814px">Newsletter Sign up</div>
<div class="abs section-title" style="left:0;width:1200px;text-align:center;top:3838px;font-size:35px">Subscribe To <span>Our Newsletter</span></div>
<div class="abs" style="left:255px;top:3910px;width:690px;height:64px;border-radius:32px;background:#fff;box-shadow:0 3px 10px rgba(0,0,0,.15)"></div>
<div class="abs" style="left:303px;top:3934px;font-size:12px;letter-spacing:1px;color:#222">Enter Email Address</div>
<div class="btn" style="left:788px;top:3910px;width:157px;height:64px;border-radius:0 32px 32px 0;font-size:14px">Subscribe</div>

<!-- footer -->
<footer class="footer">
  <div class="abs" style="left:112px;top:77px;width:198px;height:100px;border-radius:50%;background:#fff;border:4px solid var(--blue);display:flex;align-items:center;justify-content:center;font-weight:800;font-size:22px;color:var(--blue)">Pelican HVAC</div>
  <p class="abs" style="left:112px;top:196px;width:220px;font-size:13.5px;line-height:24px;letter-spacing:1px;text-align:justify">Lorem ipsum dolor sit amet, consectetur adipiscing elit, sed do eiusmod tempor incididunt.</p>

  <h4 style="left:471px;top:105px">Quick Links</h4>
  <div class="link" style="left:473px;top:140px">Home</div>
  <div class="link" style="left:473px;top:170px">About Us</div>
  <div class="link" style="left:473px;top:200px">Services</div>
  <div class="link" style="left:473px;top:229px">Team</div>
  <div class="link" style="left:473px;top:259px">Contact Us</div>

  <h4 style="left:652px;top:105px">Help Links</h4>
  <div class="link" style="left:652px;top:140px">Privacy Policy</div>
  <div class="link" style="left:652px;top:170px">Terms &amp; Conditions</div>
  <h4 style="left:652px;top:206px">Follow Us</h4>
  <svg class="abs" style="left:652px;top:243px" width="124" height="20" viewBox="0 0 124 20">
    <rect x="0" y="0" width="20" height="20" rx="3" fill="#0054AA"/>
    <rect x="26" y="0" width="20" height="20" rx="3" fill="#0054AA"/>
    <rect x="52" y="0" width="20" height="20" rx="3" fill="#0054AA"/>
    <rect x="78" y="0" width="20" height="20" rx="3" fill="#0054AA"/>
    <rect x="104" y="0" width="20" height="20" rx="3" fill="#0054AA"/>
  </svg>

  <h4 style="left:874px;top:105px">Contact Us</h4>
  <svg class="abs" style="left:874px;top:150px" width="26" height="26" viewBox="0 0 26 26"><circle cx="13" cy="13" r="12" fill="#fff"/><path d="M13 6a5 5 0 0 0-5 5c0 4 5 9 5 9s5-5 5-9a5 5 0 0 0-5-5z" fill="none" stroke="#000" stroke-width="1.8"/><circle cx="13" cy="11" r="1.8" fill="#000"/></svg>
  <div class="contact" style="left:914px;top:155px">Lorem Ipsum,Usa - 4379</div>
  <svg class="abs" style="left:874px;top:200px" width="26" height="26" viewBox="0 0 26 26"><circle cx="13" cy="13" r="12" fill="#fff"/><path d="M8 7c1-1 2-1 3 1l1 2c0 1-1 2-1 2 1 2 2 3 4 4 0 0 1-1 2-1l2 1c2 1 2 2 1 3-1 1-3 2-5 1-4-2-7-5-8-9 0-2 0-3 1-4z" fill="#000"/></svg>
  <div class="contact" style="left:914px;top:205px">555 - 014 - 2287</div>
  <svg class="abs" style="left:874px;top:251px" width="26" height="26" viewBox="0 0 26 26"><circle cx="13" cy="13" r="12" fill="#fff"/><rect x="6.5" y="8" width="13" height="10" rx="1.5" fill="none" stroke="#000" stroke-width="1.8"/><path d="M7 9l6 5 6-5" fill="none" stroke="#000" stroke-width="1.8"/></svg>
  <div class="contact" style="left:914px;top:257px">info@pelicanhvac.example</div>

  <div class="abs" style="left:112px;top:323px;width:976px;height:1px;background:#666"></div>
  <div class="abs" style="left:0;top:346px;width:1200px;text-align:center;font-size:11px;letter-spacing:.5px">Copyright &copy; 2024 Pelican HVAC. All rights reserved.</div>
</footer>

</body>
</html>
```